Business Card Design For A Renovation Contractor Company

We need a business card for a new company based in Singapore, our company name is "RB Tolvane". We are a renovation contractor that builds designs into reality. We build more of F&B restaurants, retail stores and commercial offices. We work very closely with designers. The final design should communicate to our client that we are a company that you can trust, that will plan and complete your project without giving you a headache. I like my client to remember my company as "RB". The beauty of SIMPLE is important.

Industry/Entity Type

Contractor

Requirements
Nice to have
• Black or Red base

```html
<!DOCTYPE html>
<html lang="en">
<head>
<meta charset="utf-8">
<title>RB Tolvane - Business Card</title>
<link rel="stylesheet" href="https://fonts.googleapis.com/css2?family=Arimo:wght@400&family=Didact+Gothic&family=Tinos:wght@400&display=swap">
<style>
  :root {
    --paper: #ffffff;
    --brand-red: #ec1c24;
    --deep-red: #c8161d;
    --ink: #1f1a1a;
    --grey-text: #8a8a8a;
    --crop: #6d6d6d;
    --cut-line: #5bc0eb;
    --safe-line: #a8b7b5;
    --sans: "Arimo", Arial, sans-serif;
    --display: "Didact Gothic", "Century Gothic", sans-serif;
    --serif: "Tinos", "Times New Roman", serif;
  }
  html, body { margin: 0; padding: 0; overflow: hidden; background: var(--paper); }
  .sheet { position: relative; width: 1200px; height: 504px; overflow: hidden; background: var(--paper); }
  .sheet-guides { position: absolute; inset: 0; }
  .sheet-title {
    position: absolute; top: 22px; left: 0; width: 1200px; margin: 0;
    text-align: center; font: 400 18px var(--sans); color: var(--ink);
  }
  .abs { position: absolute; margin: 0; white-space: nowrap; line-height: 1; }

  /* front */
  .holder-name { left: 97px; top: 196px; font: 400 17px/1 var(--serif); color: var(--grey-text); letter-spacing: 0.2px; }
  .holder-role { left: 97px; top: 215px; font: 400 15px/1 var(--serif); color: var(--brand-red); }
  .contact-list { left: 100px; top: 273px; list-style: none; padding: 0; font: 400 14px/17px var(--serif); color: var(--grey-text); }
  .contact-list li { display: flex; align-items: flex-start; }
  .contact-list .icon { width: 12px; height: 12px; margin: 2px 8px 0 0; flex: none; }
  .contact-list .icon-gap { width: 12px; margin-right: 8px; flex: none; }
  .brand-name { left: 341px; top: 294px; width: 206px; text-align: center; font: 400 34px/1 var(--display); color: var(--brand-red); }
  .brand-rule { left: 341px; top: 328px; width: 206px; height: 1px; background: var(--ink); }
  .brand-tagline { left: 341px; top: 331px; width: 206px; text-align: center; font: 400 13.5px/1 var(--sans); color: var(--ink); }

  /* back */
  .slogan-small { font: 400 23px/1 var(--display); color: var(--ink); letter-spacing: 0.5px; }
  .slogan-large { font: 400 56px/1 var(--display); color: var(--paper); letter-spacing: 1px; }
  .slogan-building { left: 761px; top: 208px; }
  .slogan-reality { left: 757px; top: 224px; }
  .slogan-with { left: 762px; top: 281px; }
  .slogan-plan { left: 860px; top: 268px; }
  .web-address { left: 862px; top: 335px; font: 400 17px/1 var(--serif); color: var(--ink); }
</style>
</head>
<body>
<main class="sheet">
  <h1 class="sheet-title">RB Tolvane - Business Card - 90x55 mm</h1>

  <svg class="sheet-guides" width="1200" height="504" viewBox="0 0 1200 504" aria-hidden="true">
    <rect x="70" y="130" width="503" height="307" rx="40" fill="var(--paper)" stroke="var(--cut-line)" stroke-width="1"/>
    <circle cx="70" cy="202" r="10" fill="var(--brand-red)"/>
    <circle cx="440" cy="252" r="33" fill="none" stroke="var(--ink)" stroke-width="3"/>
    <rect x="615" y="112" width="538" height="342" rx="45" fill="var(--brand-red)"/>
    <rect x="632" y="130" width="503" height="307" rx="40" fill="none" stroke="var(--safe-line)" stroke-width="1"/>
    <g stroke="var(--crop)" stroke-width="1">
      <line x1="70" y1="90" x2="70" y2="130"/>
      <line x1="30" y1="130" x2="70" y2="130"/>
      <line x1="70" y1="437" x2="70" y2="477"/>
      <line x1="30" y1="437" x2="70" y2="437"/>
      <line x1="573" y1="90" x2="573" y2="130"/>
      <line x1="573" y1="130" x2="613" y2="130"/>
      <line x1="573" y1="437" x2="573" y2="477"/>
      <line x1="573" y1="437" x2="613" y2="437"/>
      <line x1="632" y1="90" x2="632" y2="130"/>
      <line x1="632" y1="437" x2="632" y2="477"/>
      <line x1="1135" y1="90" x2="1135" y2="130"/>
      <line x1="1135" y1="130" x2="1175" y2="130"/>
      <line x1="1135" y1="437" x2="1135" y2="477"/>
      <line x1="1135" y1="437" x2="1175" y2="437"/>
    </g>
  </svg>

  <!-- front -->
  <p class="abs holder-name">CARDHOLDER NAME</p>
  <p class="abs holder-role">Designation</p>
  <ul class="abs contact-list">
    <li>
      <svg class="icon" viewBox="0 0 12 12" aria-hidden="true"><path d="M6 0.5a4 4 0 0 0-4 4c0 3 4 7 4 7s4-4 4-7a4 4 0 0 0-4-4z" fill="var(--brand-red)"/><circle cx="6" cy="4.5" r="1.5" fill="var(--paper)"/></svg>
      <span>01 01 Avenue, Suite No. 123</span>
    </li>
    <li><span class="icon-gap"></span><span>Your City, Country</span></li>
    <li>
      <svg class="icon" viewBox="0 0 12 12" aria-hidden="true"><circle cx="6" cy="6" r="6" fill="var(--brand-red)"/><path d="M3.6 3.2l1.3-.4.8 1.6-.8.6c.4.9 1 1.5 1.9 1.9l.6-.8 1.6.8-.4 1.3c-2.6 0-5-2.4-5-5z" fill="var(--paper)"/></svg>
      <span>+0 12 345 6789</span>
    </li>
    <li>
      <svg class="icon" viewBox="0 0 12 12" aria-hidden="true"><circle cx="6" cy="6" r="6" fill="var(--brand-red)"/><path d="M3.6 3.2l1.3-.4.8 1.6-.8.6c.4.9 1 1.5 1.9 1.9l.6-.8 1.6.8-.4 1.3c-2.6 0-5-2.4-5-5z" fill="var(--paper)"/></svg>
      <span>+0 12 345 6781</span>
    </li>
    <li>
      <svg class="icon" viewBox="0 0 12 12" aria-hidden="true"><rect x="3" y="0.5" width="6" height="4" fill="var(--brand-red)"/><rect x="0.5" y="5" width="11" height="6.5" fill="var(--brand-red)"/></svg>
      <span>+0 12 345 6780</span>
    </li>
    <li>
      <svg class="icon" viewBox="0 0 12 12" aria-hidden="true"><rect x="0" y="2" width="12" height="8" fill="var(--brand-red)"/><path d="M2 4h8M2 6h8M3 8h6" stroke="var(--paper)" stroke-width="0.8"/></svg>
      <span>name@rbtolvane.com</span>
    </li>
  </ul>

  <p class="abs brand-name">RB Tolvane</p>
  <div class="abs brand-rule"></div>
  <p class="abs brand-tagline">building reality with a plan</p>

  <!-- back -->
  <p class="abs slogan-small slogan-building">building</p>
  <p class="abs slogan-large slogan-reality">reality</p>
  <p class="abs slogan-small slogan-with">with a</p>
  <p class="abs slogan-large slogan-plan">plan</p>
  <p class="abs web-address">www.rbtolvane.com</p>
</main>
</body>
</html>
```